Valdane Companies Business Card Design

We need a new business card for our Private Equity Real Estate Development firm, “Valdane” and our EB-5 regional center “Thornmere Regional Center” on one card. We prefer a design that is simple, elegant, and represents the luxury products we design and build as well as the financial security and stability our successful history has produced. We are an industry leader in our field and 3rd generation family business that has evolved into an institutional quality investment platform. Considered design size is standard business card dimensions (3.5 x 2 inches with an additional 1/8 inch space for design elements or backgrounds that extend beyond the finished size of your piece.

Target Market(s)

• High net worth individuals
• Highly skilled technical workers and physicians in the US seeking investment-based immigration opportunities
• Sophisticated private equity investors
• Intermediary partners include domestic attorneys and investment brokers, as well as international agent networks
• US real estate developers

Industry/Entity Type

Finance

Contact Information for Business Card

(Providing placeholder info for personal information, please design for longer character spaces, longer names and addresses etc..)
• Logo for Valdane
• Logo for Thornmere Regional Center
• Full name: Marcus Valdane
• Job title: CEO
• Email address: mvaldane@valdanecompanies.com
• Cell phone number: +1.555.314.2287
• Office number +1.555.628.4410
• Office address: Larkfield Court 5, 4817 Vista Orilla, San Ramon, CA.
• Website: www.valdanecompanies.com

Font styles to use
Serif
Sans Serif

Colors
ec1f27
ffffff
000000

Requirements
Must have
• • Logo for Valdane
• • Logo for Thornmere Regional Center
• - Use rounded corners
• (See .ai file included for logos)
Nice to have
• • Simple, elegant design
• • Aesthetically compatible with our website design (www.valdanecompanies.com)
• • Color palette including but not limited to white, black, and red (as per logos)
Should not have
• - Not too much red color
• - Do not stack both logos on top of each other

```html
<!DOCTYPE html>
<html lang="en">
<head>
<meta charset="utf-8">
<title>Valdane Companies Business Card</title>
<link href="https://fonts.googleapis.com/css2?family=Cinzel:wght@600&family=Source+Sans+3:wght@400;600&display=swap" rel="stylesheet">
<style>
  :root {
    --backdrop: #7b7b7b;
    --card-white: #ececec;
    --ink: #2e2e2e;
    --ink-soft: #3a3a3a;
    --rule: #bdbdbd;
    --brand-red: #a31c33;
    --paper: #ffffff;
  }
  * { margin: 0; padding: 0; box-sizing: border-box; }
  html, body { width: 1200px; height: 1200px; overflow: hidden; }
  body { background: var(--backdrop); position: relative; font-family: "Source Sans 3", sans-serif; }

  .card {
    position: absolute;
    top: 310px;
    width: 364px;
    height: 594px;
    box-shadow: 2px 3px 6px rgba(0,0,0,0.35);
  }
  .card--front { left: 234px; background: var(--card-white); color: var(--ink); text-align: center; }
  .card--back { left: 627px; width: 369px; background: var(--brand-red); color: var(--paper); text-align: center; }

  .brand-name {
    font-family: "Cinzel", serif;
    font-weight: 600;
    color: var(--ink);
    position: absolute;
    left: 0; right: 0;
  }
  .brand-name__main { top: 196px; font-size: 44px; letter-spacing: 1px; }
  .brand-name__sub { top: 254px; font-size: 15px; letter-spacing: 7px; }

  .person-name {
    position: absolute; top: 338px; left: 0; right: 0;
    font-family: "Cinzel", serif; font-weight: 600; font-size: 22px; letter-spacing: 0.5px;
  }
  .person-title { position: absolute; top: 367px; left: 0; right: 0; font-size: 15px; }

  .rule { position: absolute; left: 69px; width: 226px; height: 1px; background: var(--rule); }
  .rule--top { top: 393px; }
  .rule--bottom { top: 497px; }

  .contact-list {
    position: absolute; top: 402px; left: 0; right: 0;
    list-style: none; font-size: 16px; line-height: 21.5px; color: var(--ink-soft);
  }
  .contact-list b { font-weight: 600; }

  .address {
    position: absolute; top: 506px; left: 0; right: 0;
    font-size: 16px; line-height: 21px; color: var(--ink-soft);
  }

  .center-name {
    position: absolute; left: 0; right: 0;
    font-family: "Cinzel", serif; font-weight: 600; color: var(--paper);
  }
  .center-name__main { top: 470px; font-size: 43px; letter-spacing: 0.5px; }
  .center-name__sub { top: 524px; font-size: 15px; letter-spacing: 7px; }
</style>
</head>
<body>
  <section class="card card--front" aria-label="Valdane Capital card front">
    <div class="brand-name brand-name__main">Valdane</div>
    <div class="brand-name brand-name__sub">CAPITAL</div>

    <div class="person-name">MARCUS VALDANE</div>
    <div class="person-title">CEO</div>
    <div class="rule rule--top"></div>
    <ul class="contact-list">
      <li><b>P:</b> +1.555.314.2287</li>
      <li><b>M:</b> +1.555.628.4410</li>
      <li><b>E:</b>&nbsp; mvaldane@valdanecompanies.com</li>
      <li><b>W:</b> www.valdanecompanies.com</li>
    </ul>
    <div class="rule rule--bottom"></div>
    <p class="address">Larkfield Court 5, 4817 Vista<br>Orilla, San Ramon, CA</p>
  </section>

  <section class="card card--back" aria-label="Thornmere Regional Center card back">
    <div class="center-name center-name__main">Thornmere</div>
    <div class="center-name center-name__sub">REGIONAL CENTER</div>
  </section>
</body>
</html>
```